Harborline Renewal Business Card Design

Professional and clean design. The design colors should flow with the logo. Two-sided card with the website on the back which is:

www.HarborlineRenewal.example.

"Specializing in Water Damage Restoration"

On the front I need the name, email, phone, and logo.

Name: Darnell Quisby
Email: Darnell@HarborlineRenewal.example
Phone: 555-318-2046 for now

I only have the Preview and Thumbnail right now but should have the source files uploaded within a day or two.

Target Market(s)

Flood victims, home owners with water damage from busted pipes etc...

Industry/Entity Type

Business

Contact Information for Business Card

Name: Darnell Quisby

Font styles to use
Serif
Sans Serif

Requirements
Must have
• Business Card Details Info

```html
<!DOCTYPE html>
<html lang="en">
<head>
<meta charset="utf-8">
<title>Harborline Renewal Business Card</title>
<link href="https://fonts.googleapis.com/css2?family=Cinzel:wght@400;600&family=Source+Sans+3:wght@400&display=swap" rel="stylesheet">
<style>
  :root {
    --stage: #1b1b1b;
    --card-blue: #2a98d8;
    --brand-blue: #2b8fd5;
    --band-blue: #5ec2f0;
    --soft-blue: #7cc3ec;
    --white: #ffffff;
    --faint: rgba(255, 255, 255, 0.1);
  }
  * { margin: 0; padding: 0; box-sizing: border-box; }
  html, body {
    width: 1200px; height: 741px; overflow: hidden;
    background: var(--stage);
  }
  .stage { position: relative; width: 1200px; height: 741px; }
  .card {
    position: absolute; top: 236px; width: 494px; height: 282px; overflow: hidden;
  }

  .wordmark { font-family: "Cinzel", serif; font-weight: 600; text-align: center; }
  .wordmark-main { display: block; letter-spacing: 1px; }
  .wordmark-sub {
    display: flex; align-items: center; justify-content: center; gap: 4px;
    font-weight: 400; letter-spacing: 5px;
  }
  .wordmark-sub::before, .wordmark-sub::after {
    content: ""; width: 26px; height: 1.5px; background: currentColor;
  }

  /* Back side */
  .card-back { left: 87px; background: var(--card-blue); color: var(--white); }
  .back-emblem-area {
    position: absolute; left: 80px; top: -10px; width: 340px; height: 340px;
    border-radius: 50%; background: var(--faint);
  }
  .back-mark {
    position: absolute; left: 212px; top: 56px; width: 70px; height: 70px;
    border-radius: 50%; background: var(--white);
  }
  .back-wordmark { position: absolute; left: 0; right: 0; top: 139px; }
  .back-wordmark .wordmark-main { font-size: 33px; line-height: 34px; }
  .back-wordmark .wordmark-sub { font-size: 14px; line-height: 16px; margin-top: 0; }
  .back-tagline {
    position: absolute; left: 0; right: 0; top: 190px; text-align: center;
    font-family: "Source Sans 3", sans-serif; font-size: 13px; line-height: 16px;
  }
  .back-rule { position: absolute; top: 247px; height: 1px; background: var(--white); }
  .back-rule.left { left: 0; width: 138px; }
  .back-rule.right { left: 357px; width: 137px; }
  .back-url {
    position: absolute; left: 0; right: 0; top: 239px; text-align: center;
    font-family: "Source Sans 3", sans-serif; font-size: 13px; line-height: 16px;
  }

  /* Front side */
  .card-front { left: 619px; background: var(--white); }
  .name-band {
    position: absolute; left: 0; top: 168px; width: 280px; height: 30px;
    background: var(--band-blue);
  }
  .contact-panel {
    position: absolute; left: 0; top: 198px; width: 494px; height: 84px;
    background: var(--brand-blue);
  }
  .roof-art {
    position: absolute; left: 280px; top: 87px; width: 214px; height: 111px;
    background: linear-gradient(180deg, var(--soft-blue), var(--brand-blue));
  }
  .front-wordmark { position: absolute; left: 26px; top: 32px; color: var(--brand-blue); }
  .front-wordmark .wordmark-main { font-size: 31px; line-height: 32px; }
  .front-wordmark .wordmark-sub { font-size: 13px; line-height: 16px; }
  .front-tagline {
    position: absolute; left: 30px; top: 98px; color: var(--brand-blue);
    font-family: "Source Sans 3", sans-serif; font-size: 12px; line-height: 15px;
  }
  .person-name {
    position: absolute; left: 26px; top: 170px; color: var(--white);
    font-family: "Cinzel", serif; font-weight: 600; font-size: 19px; line-height: 26px;
    letter-spacing: 1px;
  }
  .contact-list {
    position: absolute; left: 26px; top: 210px; list-style: none;
    font-family: "Source Sans 3", sans-serif; font-size: 14.5px; color: var(--white);
  }
  .contact-item { display: flex; align-items: center; height: 18.5px; }
  .contact-icon { width: 14px; height: 14px; margin-right: 8px; flex: none; }
</style>
</head>
<body>
<main class="stage">

  <section class="card card-back" aria-label="Card back">
    <div class="back-emblem-area" role="img" aria-label="Faint large brand emblem"></div>
    <div class="back-mark" aria-hidden="true"></div>
    <h1 class="wordmark back-wordmark">
      <span class="wordmark-main">HARBORLINE</span>
      <span class="wordmark-sub">RENEWAL</span>
    </h1>
    <p class="back-tagline">Specializing in Water Damage Restoration</p>
    <span class="back-rule left"></span>
    <p class="back-url">www.HarborlineRenewal.example</p>
    <span class="back-rule right"></span>
  </section>

  <section class="card card-front" aria-label="Card front">
    <div class="name-band"></div>
    <div class="contact-panel"></div>
    <div class="roof-art" role="img" aria-label="House roof illustration with window and chimney"></div>
    <h2 class="wordmark front-wordmark">
      <span class="wordmark-main">HARBORLINE</span>
      <span class="wordmark-sub">RENEWAL</span>
    </h2>
    <p class="front-tagline">Specializing in Water Damage Restoration</p>
    <p class="person-name">Darnell Quisby</p>
    <ul class="contact-list">
      <li class="contact-item">
        <svg class="contact-icon" viewBox="0 0 14 14" aria-hidden="true">
          <rect width="14" height="14" fill="var(--white)"/>
          <path d="M3 4.5 Q7 2 11 4.5 L10 6 L8.5 5.2 L8.5 6 H5.5 L5.5 5.2 L4 6 Z M4 7.5 H10 V11 H4 Z" fill="var(--brand-blue)"/>
        </svg>
        <span>555-318-2046</span>
      </li>
      <li class="contact-item">
        <svg class="contact-icon" viewBox="0 0 14 14" aria-hidden="true">
          <rect width="14" height="14" fill="var(--white)"/>
          <rect x="2.5" y="3.5" width="9" height="7" fill="none" stroke="var(--brand-blue)" stroke-width="1.2"/>
          <path d="M2.5 3.5 L7 7.5 L11.5 3.5 M2.5 10.5 L5.5 7 M11.5 10.5 L8.5 7" fill="none" stroke="var(--brand-blue)" stroke-width="1.1"/>
        </svg>
        <span>Darnell@HarborlineRenewal.example</span>
      </li>
      <li class="contact-item">
        <svg class="contact-icon" viewBox="0 0 14 14" aria-hidden="true">
          <rect width="14" height="14" fill="var(--white)"/>
          <circle cx="7" cy="7" r="4.5" fill="none" stroke="var(--brand-blue)" stroke-width="1.1"/>
          <path d="M2.5 7 H11.5 M7 2.5 V11.5 M7 2.5 Q4.5 7 7 11.5 M7 2.5 Q9.5 7 7 11.5" fill="none" stroke="var(--brand-blue)" stroke-width="0.9"/>
        </svg>
        <span>www.HarborlineRenewal.example</span>
      </li>
    </ul>
  </section>

</main>
</body>
</html>
```